bright as morning project

I need 2 stickers (lid and side) for a see-through rectangular plastic container that holds a whole, free range chicken.
Updates

CHANGE OF PACKAGING

 

we are unable to source the clear, rectangular, see-throughcontainer in the previously attached file and have to amend our packagingstrategy.

 

 

 

UPDATED STRATEGY:

 

we intend to use one of the 'french style' cardboard typewrap-around stickers as shown in the new attachments I have posted. australiansupermarkets would not accept this type of thin cardboard on its own as is applicablein france and for that reason we intend insert the wrapped-around cardboard stickeredwhole chicken on a poly styrene tray and then placed in a clear plastic cellophanebag with a twisted tie as shown the 'varèn brand' attached file.

 

the other technical requirements (barcode, kilograms, netpricing, etc.) remain the same

 

 

also note:

 

when using our existing 'pure table' logo, please removethe text:

 

rabbi tovel hanley oster

potential brand names:

1. bright as morning
2. merry osgood

cardboard label needs to be a ' wrap around label' (wrapped, north-south) as shown in the following 
attached files:

'wrap around label'  + 'wrap around label b'

we like the 'merry osgood' FONT and primary yellow background. 

dorvin 

Target Market(s)

free range poultry consumers (GREENIES) jews (pure table), affluent, up market, product is priced at the premium end of the market

Industry/Entity Type

Plastic

Requirements
Must have
• in order of importance...

LID LABEL STICKER-(see attached photo)
logo name (bright as morning)
free range
sanitised with kosher rock salt
extra fresh
long shelf life
kosher certified

SIDE LABEL STICKER- (see attached photo)
country of manufacture
processors contact details
(7 pellham lane brisbury east 3172 0472 836 204 www.brightasmorning.com.au)
barcode
product description (whole, drumsticks, filets, etc)
kosher status declaration and kosher logo (see attachment)
price per kilogram section
net weight per kilogram section
use by date
total price
refrigeration advise-store below 5degreesC

note:

the whole chicken is wrapped in light BROWN colored butchers paper and tied with a green ribbon. the customer can only see the raw chicken at each end.

```html
<!DOCTYPE html>
<html lang="en">
<head>
<meta charset="utf-8">
<title>Merry Osgood – Wrap-around Label</title>
<link rel="stylesheet" href="https://fonts.googleapis.com/css2?family=Rye&family=Arimo:wght@400;700&display=swap">
<style>
  :root {
    --ink: #171819;
    --text-dark: #2b2119;
    --orange: #e8821e;
    --orange-deep: #e67a1c;
    --amber: #f3a51c;
    --yellow: #fde31c;
    --kosher-red: #7a2424;
    --white: #ffffff;
    --barcode-grey: #e6e6e8;
    --barcode-text: #333333;
    --frame: #c9c9c9;
  }
  * { margin: 0; padding: 0; box-sizing: border-box; }
  html, body { width: 1200px; height: 900px; overflow: hidden; background: var(--white); }
  .label-sheet {
    position: relative;
    width: 1200px;
    height: 900px;
    border: 1px solid var(--frame);
    font-family: "Arimo", Arial, sans-serif;
    font-weight: 700;
    color: var(--text-dark);
  }
  .label-shapes { position: absolute; inset: 0; }
  .t { position: absolute; white-space: nowrap; text-align: center; transform: translateX(-50%); line-height: 1; }

  .brand-name {
    left: 360px; top: 282px;
    font-family: "Rye", Georgia, serif;
    font-weight: 400;
    font-size: 70px;
    line-height: 96px;
    color: var(--white);
    letter-spacing: 1px;
  }
  .product-type { left: 357px; top: 506px; font-size: 24px; color: var(--white); letter-spacing: 1px; }
  .origin { left: 357px; top: 546px; font-size: 17px; }
  .kosher-mark {
    left: 358px; top: 596px;
    display: flex; align-items: center; gap: 8px;
    font-size: 22px; color: var(--kosher-red);
  }
  .kosher-mark .mark-square { width: 16px; height: 16px; background: var(--kosher-red); }
  .kosher-note { left: 359px; top: 638px; font-size: 15px; }

  .price-panel {
    position: absolute; left: 137px; top: 667px; width: 443px; height: 71px;
    background: var(--white);
  }
  .price-field { position: absolute; font-size: 16px; line-height: 1; }
  .price-field.best-before { left: 28px; top: 15px; }
  .price-field.net-weight { left: 253px; top: 15px; }
  .price-field.price-kg { left: 28px; top: 44px; }
  .price-field.total-price { left: 253px; top: 44px; }

  .barcode-panel {
    position: absolute; left: 612px; top: 613px; width: 50px; height: 155px;
    background: var(--barcode-grey);
    display: flex; align-items: center; justify-content: center;
  }
  .barcode-panel span {
    display: block;
    transform: rotate(-90deg);
    font-size: 15px; font-weight: 400;
    color: var(--barcode-text);
    white-space: nowrap;
  }

  .storage { left: 358px; top: 752px; font-size: 16px; }
  .contact { left: 365px; top: 792px; font-size: 16px; line-height: 20px; }

  .claim { left: 912px; font-size: 41px; line-height: 42px; }
  .claim.fresh { top: 148px; }
  .claim.range { top: 238px; }
  .claim.salt { top: 326px; }
  .claim.shelf { top: 459px; }
  .claim.certified { top: 549px; }
</style>
</head>
<body>
<div class="label-sheet">
  <svg class="label-shapes" width="1200" height="900" viewBox="0 0 1200 900">
    <defs>
      <linearGradient id="sideFill" x1="0" y1="0" x2="0" y2="1">
        <stop offset="0" stop-color="#f7c21c"/>
        <stop offset="0.5" stop-color="#f0a01e"/>
        <stop offset="1" stop-color="#e8821e"/>
      </linearGradient>
      <linearGradient id="lidFill" x1="0" y1="0" x2="0" y2="1">
        <stop offset="0" stop-color="#e67a1c"/>
        <stop offset="0.55" stop-color="#f3a51c"/>
        <stop offset="1" stop-color="#fde31c"/>
      </linearGradient>
      <linearGradient id="divider" x1="0" y1="0" x2="1" y2="0">
        <stop offset="0" stop-color="#fff" stop-opacity="0"/>
        <stop offset="0.5" stop-color="#fff" stop-opacity="0.9"/>
        <stop offset="1" stop-color="#fff" stop-opacity="0"/>
      </linearGradient>
    </defs>

    <path class="side-label-body" role="img" aria-label="Yellow and orange diamond-check background pattern"
      d="M175,125 L548,125 C562,270 640,390 668,520 C682,590 692,650 690,700 C680,790 520,845 360,845 C200,845 45,790 40,700 C40,630 50,560 62,500 C90,380 160,260 175,125 Z"
      fill="url(#sideFill)"/>
    <path class="brand-panel" d="M180,485 V125 Q360,78 540,125 V485 Z" fill="var(--ink)"/>
    <polygon class="product-band" points="56,495 655,495 667,538 46,538" fill="var(--ink)"/>

    <path class="lid-label-body"
      d="M660,140 Q915,78 1170,135 C1162,330 1092,500 1066,640 Q915,745 762,640 C738,500 668,330 660,140 Z"
      fill="url(#lidFill)"/>
    <g class="lid-dividers" fill="url(#divider)">
      <rect x="750" y="213" width="325" height="3"/>
      <rect x="750" y="303" width="325" height="3"/>
      <rect x="750" y="435" width="325" height="3"/>
      <rect x="750" y="529" width="325" height="3"/>
    </g>
  </svg>

  <div class="t brand-name">MERRY<br>OSGOOD</div>
  <div class="t product-type">WHOLE&nbsp; CHICKEN</div>
  <div class="t origin">Product of Australia</div>
  <div class="t kosher-mark"><span class="mark-square"></span><span>pure table</span></div>
  <div class="t kosher-note">Kosher Certified</div>

  <div class="price-panel">
    <span class="price-field best-before">Best before</span>
    <span class="price-field net-weight">Net Wt.</span>
    <span class="price-field price-kg">Price Per KG.</span>
    <span class="price-field total-price">Total Price</span>
  </div>

  <div class="barcode-panel"><span>barcode</span></div>

  <div class="t storage">Store below 5 degree C</div>
  <div class="t contact">7 Pellham Lane Brisbury East 3172.<br>www.brightasmorning.com.au</div>

  <div class="t claim fresh">Extra Fresh</div>
  <div class="t claim range">Free Range</div>
  <div class="t claim salt">Sanitised with<br>Kosher Rock Salt</div>
  <div class="t claim shelf">Long Shelf&nbsp; Life</div>
  <div class="t claim certified">Kosher<br>Certified</div>
</div>
</body>
</html>
```